Luxury Real Estate Website, Midwest, United States

We need web design services for a luxury website. We need IDX Integration with our MLS. We want this to be a very simple website with amazing graphics. We want it to link up with our MailChimp account in order to generate leads through a "More Information" Pop up on the main page. We want the main page to be covered with one large graphic that is a rolling slideshow of active listings of $400,000 and up from the IDX Integration. We need this website to give a very exclusive and sleek look. Lots of black is good... I will upload our logos in Black and Silver. We will also need an "About" page that we are going to call "Qeno Info". We want our graphics to be extremely impressive. Keep in mind, we are a company in the Midwest of the United States, and our real estate has a different look than homes in California or Florida. We need graphics that are realistic for the Midwest, yet still high-end.
Target Market(s)
Luxury Homeowners in the Midwest United States. The graphics needs to be pristine.
Industry/Entity Type
Real Estate
Coding
Coded - Design and coding required
Number of Pages Required
3 page
Requirements
Must have
- Large graphics with IDX Integration. The photos of real estate need to represent real estate that is common in the Midwest, United States. We also need MailChimp integration. We need a pop up that is titled "My Free Market Analysis" that makes them fill out a contact form asking for Full Name, Email Address, Phone Number and Address. This needs to be a pop up on the front page and will integrate with our MailChimp account. We also need a page called "About Qe No Home". And another page where clients can download informational PDFs. The main component needs to be a front page search engine connected with the IDX to access active listings from our MLS. I attached our logos and a sample front page of a website. I would love for ours to look similar.
Nice to have
- Lake House photos on midwest lakes are a plus.
Should not have
- Should not have clutter. This website needs to be clean, luxurious and exclusive.

```html
<!DOCTYPE html>
<html lang="en">
<head>
<meta charset="utf-8">
<title>Hearth Realty Group – My Free Market Analysis</title>
<link href="https://fonts.googleapis.com/css2?family=Lato:wght@300;400;700&display=swap" rel="stylesheet">
<style>
:root{
  --ink:#111;
  --white:#fff;
  --page:#d9d9dd;
  --band:#b4b4b6;
  --testi:#d6d6d8;
  --foot:#cfcfd1;
  --card:#eeeeef;
  --muted:#777;
  --line:#222;
  --sky:#9dbad3;
  --haze:#c9d6df;
  --leaf:#5f7a45;
  --leaf-dark:#34442c;
  --water:#6f8a9c;
  --water-dark:#43576a;
  --brick:#8a4a36;
  --roof:#4b3a32;
  --modal:#c5d3e8;
  --veil:rgba(0,0,0,.72);
}
*{box-sizing:border-box;margin:0;padding:0}
html,body{width:1200px;height:2546px;overflow:hidden}
body{font-family:'Lato',sans-serif;background:var(--page);color:var(--ink);position:relative}

/* header */
.site-header{position:absolute;left:0;top:0;width:1200px;height:97px;background:var(--white)}
.brand{position:absolute;left:127px;top:36px;display:flex;align-items:center;gap:10px;font-size:19px;font-weight:400;letter-spacing:1px;color:var(--ink);white-space:nowrap}
.brand-mark{width:12px;height:12px;background:var(--ink)}
.main-nav{position:absolute;top:43px;left:0;font-size:14px;text-transform:uppercase;color:#444}
.main-nav span{position:absolute;white-space:nowrap}

/* hero */
.hero{position:absolute;left:0;top:97px;width:1200px;height:629px;
  background:linear-gradient(180deg,var(--sky) 0%,var(--haze) 22%,var(--leaf) 42%,var(--brick) 52%,var(--leaf-dark) 62%,var(--water) 78%,var(--water-dark) 100%)}
.slider-dots{position:absolute;left:1087px;top:226px}
.slider-dots i{display:block;width:13px;height:13px;border:2px solid var(--white);border-radius:50%;margin-bottom:11px}

/* services */
.service{position:absolute;top:626px;width:309px;height:232px;background:var(--card);border:1px solid #ddd;text-align:center}
.service svg{margin-top:28px}
.service h3{font-size:19px;font-weight:400;margin-top:14px;letter-spacing:.5px}
.service p{font-size:12px;line-height:18px;color:var(--muted);padding:0 40px;margin-top:10px}

/* about */
.about-photo{position:absolute;left:117px;top:978px;width:477px;height:305px;
  background:linear-gradient(180deg,var(--haze) 0%,var(--sky) 15%,var(--brick) 35%,var(--roof) 48%,var(--leaf) 58%,var(--water-dark) 75%,var(--water) 100%)}
.about-box{position:absolute;left:501px;top:945px;width:585px;height:375px;border:2px solid var(--line)}
.about-box h2{position:absolute;left:125px;top:50px;font-size:32px;font-weight:400;line-height:36px;white-space:nowrap}
.about-box h2 small{display:block;font-size:25px;line-height:30px}
.about-box p{position:absolute;left:125px;width:430px;font-size:12px;line-height:20px;color:var(--muted)}
.btn-outline{position:absolute;left:127px;top:282px;width:155px;height:41px;border:2px solid var(--line);font-size:15px;display:flex;align-items:center;justify-content:center;text-transform:uppercase}

/* featured */
.featured{position:absolute;left:0;top:1403px;width:1200px;height:498px;background:var(--band)}
.featured-notch{position:absolute;left:550px;top:-1px;width:0;height:0;border-left:50px solid transparent;border-right:50px solid transparent;border-top:30px solid var(--page)}
.section-title{position:absolute;width:1200px;text-align:center;font-size:26px;font-weight:400;letter-spacing:.5px}
.property{position:absolute;top:105px;width:229px;height:310px}
.property.lake{background:linear-gradient(180deg,var(--leaf-dark) 0%,var(--leaf) 20%,var(--brick) 45%,var(--roof) 65%,var(--water) 100%)}
.property.white{background:linear-gradient(180deg,var(--haze) 0%,var(--leaf) 25%,#d8d8d2 45%,#8c8f8a 65%,var(--leaf-dark) 100%)}
.property.gable{background:linear-gradient(180deg,var(--sky) 0%,var(--leaf) 30%,#5a6470 50%,#c9b89a 72%,var(--leaf-dark) 100%)}
.property.estate{background:linear-gradient(180deg,#e0b870 0%,#9a7a4a 30%,var(--leaf) 60%,var(--leaf-dark) 100%)}
.property .caption{position:absolute;left:0;bottom:0;width:100%;height:70px;background:rgba(0,0,0,.55);color:var(--white);padding:12px 20px}
.property h4{font-size:19px;font-weight:400}
.property p{font-size:12px;color:#ccc;margin-top:2px;white-space:nowrap}
.property .corner{position:absolute;right:6px;bottom:6px;width:8px;height:8px;border-right:2px solid #ddd;border-bottom:2px solid #ddd}

/* testimonials */
.testimonials{position:absolute;left:0;top:1901px;width:1200px;height:481px;background:var(--testi)}
.quote-card{position:absolute;top:145px;width:297px;height:186px;background:var(--white);border:1px solid #ccc;padding:22px 28px 0 58px;font-size:12px;line-height:25px;color:var(--muted);font-style:italic}
.quote-card::before{content:"\201C";position:absolute;left:22px;top:8px;font-size:48px;color:#999;font-style:normal}
.author{position:absolute;top:349px;display:flex;align-items:center;gap:12px}
.avatar{width:50px;height:50px;border-radius:50%;background:#b39a86}
.author b{display:block;font-size:14px;font-weight:400;color:var(--ink)}
.author span{font-size:12px;color:var(--muted)}

/* footer */
.site-footer{position:absolute;left:0;top:2382px;width:1200px;height:164px;background:var(--foot)}
.footer-brand{position:absolute;left:120px;top:58px;display:flex;align-items:center;gap:10px;font-size:24px;color:#555;letter-spacing:1px;white-space:nowrap}
.footer-brand .brand-mark{background:#555}
.footer-nav{position:absolute;left:402px;top:60px;font-size:12px;color:#444;text-transform:uppercase;display:flex;gap:26px;white-space:nowrap}
.copyright{position:absolute;left:402px;top:90px;font-size:12px;color:#555}
.social{position:absolute;top:60px;width:16px;height:16px;border-radius:50%;background:#444}

/* overlay + modal */
.veil{position:absolute;inset:0;background:var(--veil)}
.modal{position:absolute;left:230px;top:134px;width:752px;height:412px;background:var(--modal)}
.modal-frame{position:absolute;left:14px;top:15px;width:724px;height:382px;border:1px solid #222}
.modal-badge{position:absolute;left:332px;top:-42px;width:88px;height:88px;border-radius:50%;background:var(--ink);border:4px solid var(--white)}
.modal-close{position:absolute;left:702px;top:33px}
.modal h2{position:absolute;left:0;top:71px;width:752px;text-align:center;font-size:30px;font-weight:400}
.field-label{position:absolute;font-size:15px;text-transform:uppercase}
.field{position:absolute;height:44px;width:326px;background:var(--white);border:1px solid #333}
.btn-submit{position:absolute;left:47px;top:300px;width:657px;height:53px;background:var(--ink);color:var(--white);font-size:22px;display:flex;align-items:center;justify-content:center;text-transform:uppercase}
</style>
</head>
<body>

<header class="site-header">
  <div class="brand"><span class="brand-mark"></span>HEARTH REALTY GROUP</div>
  <nav class="main-nav">
    <span style="left:463px;color:#111">Home</span>
    <span style="left:540px">Qeno Info</span>
    <span style="left:650px">About Qe No Home</span>
    <span style="left:827px">Downloads</span>
    <span style="left:955px">Contact Us</span>
  </nav>
</header>

<section class="hero" role="img" aria-label="Slideshow photo of brick lakeside homes on a Midwest lake under a blue sky">
  <div class="slider-dots"><i></i><i></i><i></i><i></i></div>
</section>

<div class="service" style="left:117px">
  <svg width="60" height="56" viewBox="0 0 60 56" fill="none" stroke="#333" stroke-width="2"><path d="M6 26 30 6l24 20M12 22v30h36V22M24 52V36h12v16"/></svg>
  <h3>LUXURY PROPERTY</h3>
  <p>Class aptent taciti sociosqu ad litora torquent per conubia nostra per inceptos hymenaeos proin nulla arcu</p>
</div>
<div class="service" style="left:446px">
  <svg width="60" height="56" viewBox="0 0 60 56" fill="none" stroke="#333" stroke-width="2"><path d="M14 24 32 8l18 16M18 20v20h28V20M4 46h16l10 6 24-10"/></svg>
  <h3>BUY &amp; SELLING</h3>
  <p>Class aptent taciti sociosqu ad litora torquent per conubia nostra per inceptos hymenaeos proin nulla arcu</p>
</div>
<div class="service" style="left:773px">
  <svg width="60" height="56" viewBox="0 0 60 56" fill="none" stroke="#333" stroke-width="2"><circle cx="20" cy="30" r="7"/><path d="M6 54c0-10 6-14 14-14s14 4 14 14M32 4h24v16H44l-6 6v-6h-6z"/></svg>
  <h3>QENO INFO</h3>
  <p>Class aptent taciti sociosqu ad litora torquent per conubia nostra per inceptos hymenaeos proin nulla arcu</p>
</div>

<div class="about-photo" role="img" aria-label="Photo of a brick lake house with green lawn reflected in still water"></div>
<div class="about-box">
  <h2>ABOUT HEARTH<small>REALTY GROUP</small></h2>
  <p style="top:130px">Praesent elementum est at tellus nec ultricies ut amet porttitor mattis enim in massa libero interdum nec interdum vel blandit sed nulla.</p>
  <p style="top:190px">In ullamcorper est eget tempor cursus neque mi consectetuer mica ultricies massa est sed nisl class aptent taciti sociosqu ad litora torquent per conubia nostra per inceptos hymenaeos proin nulla.</p>
  <div class="btn-outline">Read More</div>
</div>

<section class="featured">
  <div class="featured-notch"></div>
  <h2 class="section-title" style="top:50px">FEATURED PROPERTY</h2>
  <div class="property lake" style="left:117px" role="img" aria-label="Photo of a red lake cottage among trees">
    <div class="caption"><h4>Property Title</h4><p>Dictum eget fermentum et lorem</p></div><i class="corner"></i></div>
  <div class="property white" style="left:364px" role="img" aria-label="Photo of a white two-storey home">
    <div class="caption"><h4>Property Title</h4><p>Dictum eget fermentum et lorem</p></div><i class="corner"></i></div>
  <div class="property gable" style="left:610px" role="img" aria-label="Photo of a gabled family house with garage">
    <div class="caption"><h4>Property Title</h4><p>Dictum eget fermentum et lorem</p></div><i class="corner"></i></div>
  <div class="property estate" style="left:857px" role="img" aria-label="Photo of a country estate at sunset">
    <div class="caption"><h4>Property Title</h4><p>Dictum eget fermentum et lorem</p></div><i class="corner"></i></div>
</section>

<section class="testimonials">
  <h2 class="section-title" style="top:80px">TESTIMONIALS</h2>
  <div class="quote-card" style="left:105px">Morbi dolor dictum viverra at gravida mi lobortis in nisl blandit eget arcu Morbi porta libero at ullamcorper nonummy nisl ligula pulvinar metus eget</div>
  <div class="quote-card" style="left:439px">Morbi dolor dictum viverra at gravida mi lobortis in nisl blandit eget arcu Morbi porta libero at ullamcorper nonummy nisl ligula pulvinar metus eget</div>
  <div class="quote-card" style="left:774px">Morbi dolor dictum viverra at gravida mi lobortis in nisl blandit eget arcu Morbi porta libero at ullamcorper nonummy nisl ligula pulvinar metus eget</div>
  <div class="author" style="left:115px"><div class="avatar" role="img" aria-label="Client portrait"></div><div><b>By Author Name</b><span>City Location</span></div></div>
  <div class="author" style="left:451px"><div class="avatar" role="img" aria-label="Client portrait"></div><div><b>By Author Name</b><span>City Location</span></div></div>
  <div class="author" style="left:786px"><div class="avatar" role="img" aria-label="Client portrait"></div><div><b>By Author Name</b><span>City Location</span></div></div>
</section>

<footer class="site-footer">
  <div class="footer-brand"><span class="brand-mark"></span>HEARTH REALTY</div>
  <nav class="footer-nav"><span>Home</span><span>Qeno Info</span><span>About Qe No Home</span><span>Downloads</span><span>Contact Us</span></nav>
  <div class="copyright">© 2016 Company Name. All right reserved</div>
  <span class="social" style="left:975px"></span>
  <span class="social" style="left:1013px"></span>
  <span class="social" style="left:1052px"></span>
</footer>

<div class="veil"></div>

<div class="modal" role="dialog" aria-label="My Free Market Analysis">
  <div class="modal-frame"></div>
  <div class="modal-badge"></div>
  <svg class="modal-close" width="26" height="26" viewBox="0 0 26 26" stroke="#111" stroke-width="2"><path d="M2 2l22 22M24 2 2 24"/></svg>
  <h2>MY FREE MARKET ANALYSIS</h2>
  <span class="field-label" style="left:42px;top:132px">Full Name</span>
  <span class="field-label" style="left:375px;top:132px">Email Address</span>
  <div class="field" style="left:42px;top:158px"></div>
  <div class="field" style="left:375px;top:158px"></div>
  <span class="field-label" style="left:45px;top:217px">Phone Number</span>
  <span class="field-label" style="left:378px;top:217px">Address</span>
  <div class="field" style="left:45px;top:241px"></div>
  <div class="field" style="left:378px;top:241px"></div>
  <div class="btn-submit">Submit</div>
</div>

</body>
</html>
```